Automotive component supplier needs a business card design

We need a business card design for our company called Velran Global Components Ltd based in the UK. We are a supplier of interior and exterior components to premium car manufacturers such as Corvel Ashby, Hadley Fenn, Marquist and Tavarelli. We would like to see a modern business card design that uses the colour blue.

Target Market(s)

Premium automotive car manufacturers.

Industry/Entity Type

Automotive

Contact Information for Business Card

Company Name : Velran Global Components Limited
Address: 17 Marlow Yard, Upper Heath, Warwick, CV31 8QL, United Kingdom
Web Address : www.velrancomponents-example.co.uk

Font styles to use
Other font styles liked:
• Helvetica

Colors
3176b5
0255a3
85acd3
cfdeed
cee9f5
85cae6
34a6d7
0692cd
9bcb3c

Requirements
Must have
• Clear company logo and a mixture of blue colours.
Nice to have
• A high quality modern image.
Should not have
• Multiple colours.

```html
<!DOCTYPE html>
<html lang="en">
<head>
<meta charset="utf-8">
<title>Velran Global Components – Business Card</title>
<link href="https://fonts.googleapis.com/css2?family=Arimo:wght@400;700&family=Michroma&display=swap" rel="stylesheet">
<style>
  :root {
    --stage: #1b1c1e;
    --card-blue: #0d8fd2;
    --card-blue-light: #2aa0dc;
    --white: #ffffff;
    --accent-green: #9bcb3c;
    --rule: rgba(255,255,255,0.85);
  }
  * { margin: 0; padding: 0; box-sizing: border-box; }
  html, body { width: 1200px; height: 900px; overflow: hidden; }
  body {
    background: var(--stage);
    font-family: "Arimo", Helvetica, Arial, sans-serif;
    color: var(--white);
    position: relative;
  }
  .card {
    position: absolute;
    left: 240px;
    width: 720px;
    height: 400px;
    background: var(--card-blue);
    overflow: hidden;
    box-shadow: 0 14px 30px rgba(0,0,0,0.55);
  }
  .card--front { top: 32px; }
  .card--back { top: 468px; }

  /* Front */
  .front-brand {
    position: absolute;
    left: 0; right: 0; top: 120px;
    display: flex; align-items: center; justify-content: center; gap: 18px;
  }
  .brand-name {
    font-family: "Michroma", "Arimo", sans-serif;
    font-size: 52px;
    letter-spacing: 4px;
    color: var(--white);
  }
  .brand-square {
    width: 30px; height: 30px;
    background: var(--accent-green);
    border-radius: 6px;
  }
  .front-web {
    position: absolute;
    left: 0; right: 0; top: 318px;
    display: flex; align-items: center; gap: 16px;
  }
  .front-web .rule { height: 1.5px; background: var(--rule); flex: 1; }
  .front-web .rule--short { flex: 0 0 60px; }
  .web-text { font-size: 16px; letter-spacing: 0.3px; white-space: nowrap; }
  .web-text .highlight { color: var(--accent-green); }

  /* Back */
  .back-brand {
    position: absolute;
    left: 40px; top: 40px;
    display: flex; align-items: center; gap: 14px;
  }
  .back-brand .brand-square { width: 22px; height: 22px; border-radius: 5px; }
  .back-brand .brand-name {
    font-size: 24px;
    letter-spacing: 2px;
    line-height: 1.35;
  }
  .person {
    position: absolute;
    right: 40px; top: 150px;
    text-align: right;
  }
  .person-name {
    font-family: "Michroma", "Arimo", sans-serif;
    font-size: 19px;
    letter-spacing: 2px;
    padding-bottom: 6px;
    border-bottom: 1.5px solid var(--rule);
  }
  .person-role {
    color: var(--accent-green);
    font-size: 14px;
    margin-top: 5px;
  }
  .address {
    position: absolute;
    right: 40px; top: 236px;
    text-align: right;
    font-size: 15px;
    line-height: 1.45;
  }
  .contact-rule {
    position: absolute;
    left: 40px; right: 40px; top: 290px;
    height: 1.5px; background: var(--rule);
  }
  .contacts {
    position: absolute;
    left: 40px; top: 300px;
    list-style: none;
    font-size: 15px;
    line-height: 22px;
  }
  .contacts li { display: flex; align-items: center; gap: 10px; }
  .contacts svg { width: 12px; height: 12px; fill: var(--accent-green); flex: none; }
</style>
</head>
<body>

<section class="card card--front" aria-label="Business card front">
  <div class="front-brand">
    <span class="brand-name">VELRAN</span>
    <span class="brand-square"></span>
  </div>
  <div class="front-web">
    <span class="rule"></span>
    <span class="web-text">www.<span class="highlight">velrancomponents-example</span>.co.uk</span>
    <span class="rule rule--short"></span>
  </div>
</section>

<section class="card card--back" aria-label="Business card back">
  <div class="back-brand">
    <span class="brand-square"></span>
    <span class="brand-name">VELRAN<br>GLOBAL COMPONENTS</span>
  </div>

  <div class="person">
    <div class="person-name">DORIAN ASHCOMBE</div>
    <div class="person-role">Director</div>
  </div>

  <address class="address" style="font-style:normal">
    17 Marlow Yard, Upper Heath<br>
    Warwick, CV31 8QL, UK
  </address>

  <div class="contact-rule"></div>

  <ul class="contacts">
    <li>
      <svg viewBox="0 0 12 12" aria-hidden="true"><path d="M2.5 1 L4.5 1 L5 3.5 L3.8 4.4 Q4.8 6.8 7.6 8.2 L8.5 7 L11 7.5 L11 9.5 Q10.5 11 9 11 Q1 10 1 2.5 Q1 1 2.5 1 Z"/></svg>
      780 555-0142
    </li>
    <li>
      <svg viewBox="0 0 12 12" aria-hidden="true"><path d="M3.5 0.5 H8.5 Q9.5 0.5 9.5 1.5 V10.5 Q9.5 11.5 8.5 11.5 H3.5 Q2.5 11.5 2.5 10.5 V1.5 Q2.5 0.5 3.5 0.5 Z M3.7 2 V9 H8.3 V2 Z"/></svg>
      780 555-0187
    </li>
    <li>
      <svg viewBox="0 0 12 12" aria-hidden="true"><path d="M0.5 2.5 H11.5 V9.5 H0.5 Z M1.2 3.1 L6 6.6 L10.8 3.1 Z"/></svg>
      velrancomponents@example.com
    </li>
    <li>
      <svg viewBox="0 0 12 12" aria-hidden="true"><circle cx="6" cy="6" r="5.5"/></svg>
      www.velrancomponents-example.co.uk
    </li>
  </ul>
</section>

</body>
</html>
```